Facial Tissue Brand Logo and Design

We would like you to design a Logo for the Facial Tissue Brand "Velora" along with the box design. The pack should indicate the pack size (150 x 2 ply). Also our company logo should be present (attached) along with a barcode. The box size dimensions should be 210mm (L) x 110mm (W) x 70mm (H). We are open to all kinds of nice designs which are attractive but not overdone. Happy designing!

UPDATE:
We appreciate the designs so far... but would also love to see more options in a simple and elegent design style that would look good on a table... please see attached below links for reference purpose:

www.pictovault-example.com/image-photo/cleaning-wipes-isolated-on-white-257770819

www.pictovault-example.com/image-photo/cleaning-wipes-isolated-on-white-155326937

www.pictovault-example.com/image-photo/delicate-female-hands-pulling-tissue-out-1330426586

Happy desgining!

We appreciate the designs so far.. but would like to to see some more options.

```html
<!DOCTYPE html>
<html lang="en">
<head>
<meta charset="utf-8">
<title>Velora Facial Tissue – Box Dieline</title>
<link rel="stylesheet" href="https://fonts.googleapis.com/css2?family=Montserrat:wght@400;500;600&display=swap">
<style>
  :root {
    --page: #ffffff;
    --flap: #333336;
    --panel-dark: #1b1b1d;
    --panel-dark-mid: #2c2c2f;
    --panel-light: #3c3c3f;
    --panel-light-mid: #505053;
    --cut-line: #9a9a9e;
    --ink-light: #ffffff;
    --ink-dark: #2a2a2c;
    --window: #ffffff;
    --perforation: #3f9a5a;
  }
  html, body {
    margin: 0;
    padding: 0;
    width: 678px;
    height: 1200px;
    overflow: hidden;
    background: var(--page);
  }
  .dieline {
    position: absolute;
    left: 9px;
    top: 220px;
    width: 660px;
    height: 759px;
  }
  .flap { fill: var(--flap); stroke: var(--cut-line); stroke-width: 1.5; stroke-dasharray: 5 4; }
  .fold { stroke: var(--cut-line); stroke-width: 1.2; stroke-dasharray: 5 4; fill: none; }
  .brand-name {
    font-family: "Montserrat", sans-serif;
    font-weight: 500;
    font-size: 40px;
    letter-spacing: 2px;
  }
  .tagline {
    font-family: "Montserrat", sans-serif;
    font-weight: 500;
    font-size: 13px;
    letter-spacing: 0.3px;
  }
  .pack-size {
    font-family: "Montserrat", sans-serif;
    font-weight: 600;
    font-size: 12px;
  }
  .on-dark { fill: var(--ink-light); }
  .on-light { fill: var(--ink-dark); }
  .brand-dot-light { fill: var(--ink-light); }
  .brand-dot-dark { fill: var(--ink-dark); }
  .dispenser-window { fill: var(--window); }
  .perforation { fill: none; stroke: var(--perforation); stroke-width: 1.2; stroke-dasharray: 3 3; }
</style>
</head>
<body>
<svg class="dieline" viewBox="55 735 930 1070" xmlns="http://www.w3.org/2000/svg">
  <defs>
    <linearGradient id="pattern-dark" x1="0" y1="0" x2="1" y2="0">
      <stop offset="0" stop-color="var(--panel-dark)"/>
      <stop offset="0.5" stop-color="var(--panel-dark-mid)"/>
      <stop offset="1" stop-color="var(--panel-dark)"/>
    </linearGradient>
    <linearGradient id="pattern-light" x1="0" y1="0" x2="1" y2="0">
      <stop offset="0" stop-color="var(--panel-light)"/>
      <stop offset="0.5" stop-color="var(--panel-light-mid)"/>
      <stop offset="1" stop-color="var(--panel-light)"/>
    </linearGradient>
  </defs>

  <!-- tuck flap -->
  <path class="flap" d="M262 795 L262 765 Q262 742 285 742 L765 742 Q788 742 788 765 L788 795 Z"/>

  <!-- dust flaps -->
  <g class="dust-flaps">
    <path class="flap" d="M245 815 L95 815 Q62 815 62 848 L62 1040 Q62 1070 95 1070 L245 1070 Z"/>
    <path class="flap" d="M795 815 L945 815 Q978 815 978 848 L978 1040 Q978 1070 945 1070 L795 1070 Z"/>
    <path class="flap" d="M245 1088 L200 1108 L80 1108 Q62 1108 62 1126 L62 1245 L200 1245 L245 1262 Z"/>
    <path class="flap" d="M795 1088 L840 1108 L960 1108 Q978 1108 978 1126 L978 1245 L840 1245 L795 1262 Z"/>
    <path class="flap" d="M245 1272 L95 1272 Q62 1272 62 1305 L62 1545 Q62 1578 95 1578 L245 1578 Z"/>
    <path class="flap" d="M795 1272 L945 1272 Q978 1272 978 1305 L978 1545 Q978 1578 945 1578 L795 1578 Z"/>
    <path class="flap" d="M245 1583 L200 1600 L80 1600 Q62 1600 62 1618 L62 1745 L200 1745 L245 1758 Z"/>
    <path class="flap" d="M795 1583 L840 1600 L960 1600 Q978 1600 978 1618 L978 1745 L840 1745 L795 1758 Z"/>
  </g>

  <!-- panels with chevron pattern area -->
  <g role="img" aria-label="Bottom panel: charcoal zigzag chevron pattern">
    <rect x="245" y="795" width="550" height="290" fill="url(#pattern-dark)"/>
  </g>
  <g role="img" aria-label="Back side panel: grey zigzag chevron pattern">
    <rect x="245" y="1085" width="550" height="180" fill="url(#pattern-light)"/>
  </g>
  <g role="img" aria-label="Top panel: charcoal zigzag chevron pattern">
    <rect x="245" y="1265" width="550" height="315" fill="url(#pattern-dark)"/>
  </g>
  <g role="img" aria-label="Front side panel: grey zigzag chevron pattern">
    <rect x="245" y="1580" width="550" height="180" fill="url(#pattern-light)"/>
  </g>

  <!-- fold lines -->
  <path class="fold" d="M245 795 H795 M245 1085 H795 M245 1265 H795 M245 1580 H795 M245 795 V1760 M795 795 V1760 M245 1760 H795"/>

  <!-- bottom panel (upside down) -->
  <g class="bottom-panel" transform="rotate(180 660 900)">
    <circle class="brand-dot-light" cx="586" cy="875" r="5"/>
    <text class="brand-name on-dark" x="600" y="889">Velora</text>
    <text class="tagline on-dark" x="565" y="915">FACIAL TISSUE | ULTRA SOFT</text>
  </g>

  <!-- back side panel (upside down) -->
  <g class="back-panel" transform="rotate(180 520 1130)">
    <circle class="brand-dot-light" cx="626" cy="1106" r="5"/>
    <text class="brand-name on-dark" x="640" y="1120">Velora</text>
    <text class="tagline on-dark" x="560" y="1150">FACIAL TISSUE | ULTRA SOFT</text>
    <text class="pack-size on-dark" x="268" y="1150">150 x 2 ply</text>
  </g>

  <!-- top panel with dispenser window -->
  <g class="top-panel">
    <rect class="dispenser-window" x="350" y="1355" width="345" height="140" rx="18"/>
    <path class="perforation" d="M350 1402 A22 22 0 0 1 350 1446"/>
    <circle class="brand-dot-dark" cx="443" cy="1420" r="5"/>
    <text class="brand-name on-light" x="457" y="1434">Velora</text>
    <text class="tagline on-light" x="522" y="1472" text-anchor="middle">FACIAL TISSUE | ULTRA SOFT</text>
  </g>

  <!-- front side panel -->
  <g class="front-panel">
    <circle class="brand-dot-light" cx="606" cy="1688" r="5"/>
    <text class="brand-name on-dark" x="620" y="1702">Velora</text>
    <text class="tagline on-dark" x="592" y="1732">FACIAL TISSUE | ULTRA SOFT</text>
    <text class="pack-size on-dark" x="277" y="1736">150 x 2 ply</text>
  </g>
</svg>
</body>
</html>
```